Fern Plaza Asian Tote Bag

I need vector graphics for a bag as follows:
Bag size is 12" tall x 8" wide
Front of the bag:

Dalton's logo in metallic red in the center
The word Welcome in many different Asian languages, Korean, Mandarin, Cantonese, Japanese, Vietnamese, Arabic, Thai, Mongolian etc.
These words are to be different sizes and colors
Use metallic red, silver and white only
Background to be black
You may incorporate images or sketches on a few versions of either the silver reed bridge, a trolly car or the San Francisco Sky line
This is for a specific area of San Francisco called Fern Plaza
The back of the bag is to say:
come shop our beauty dept #daltonglow

Target Market(s)

Asian Market if San Francisco

Colors
ec1f27
cbcbcb
f5f5f5

Requirements
Must have
• Dalton's Logo
• Welcome in different Asian languages
• Metallic red, silver and or white
Nice to have
• Simplistic
• Words only
• San Fran Skyline
• Trolly car
• Silver reed bridge
Should not have
• needs to be sophisticated

```html
<!DOCTYPE html>
<html lang="en">
<head>
<meta charset="utf-8">
<title>Dalton's Fern Plaza Tote: Welcome</title>
<link rel="stylesheet" href="https://fonts.googleapis.com/css2?family=Roboto+Condensed:wght@400;500&family=Roboto:wght@300&family=Noto+Sans+KR:wght@400&family=Noto+Sans+JP:wght@400&family=Noto+Sans+SC:wght@400&family=Noto+Sans+TC:wght@400&family=Noto+Sans+Thai:wght@400&family=Noto+Naskh+Arabic:wght@400&display=swap">
<style>
  :root {
    --bg: #000000;
    --red: #ec1f27;
    --silver: #a8a8a8;
    --white: #f5f5f5;
    --latin: "Roboto Condensed", sans-serif;
    --korean: "Noto Sans KR", sans-serif;
    --japanese: "Noto Sans JP", sans-serif;
    --chinese: "Noto Sans SC", sans-serif;
    --cantonese: "Noto Sans TC", sans-serif;
    --thai: "Noto Sans Thai", sans-serif;
    --arabic: "Noto Naskh Arabic", serif;
  }
  * { margin: 0; padding: 0; box-sizing: border-box; }
  html, body { width: 800px; height: 1200px; overflow: hidden; background: var(--bg); }
  .tote-front { position: relative; width: 800px; height: 1200px; background: var(--bg); }

  .welcome-stack {
    position: absolute; left: 60px; right: 60px; top: 330px;
    display: flex; flex-direction: column; align-items: center; gap: 14px;
  }
  .row { display: flex; align-items: baseline; justify-content: center; gap: 28px; }
  .word { line-height: 1.1; white-space: nowrap; }

  .red { color: var(--red); }
  .silver { color: var(--silver); }
  .white { color: var(--white); }

  .latin { font-family: var(--latin); font-weight: 500; letter-spacing: 1px; }
  .korean { font-family: var(--korean); }
  .japanese { font-family: var(--japanese); }
  .chinese { font-family: var(--chinese); }
  .cantonese { font-family: var(--cantonese); }
  .thai { font-family: var(--thai); }
  .arabic { font-family: var(--arabic); direction: rtl; }

  .welcome-main {
    font-family: var(--latin); font-weight: 400; font-size: 124px;
    letter-spacing: 6px; line-height: 1; color: var(--white);
  }
  .rule { width: 520px; height: 2px; background: var(--red); }

  .brand { position: absolute; left: 376px; top: 1060px; display: flex; align-items: center; gap: 20px; }
  .brand-dot { width: 64px; height: 64px; border-radius: 50%; background: var(--red); }
  .brand-name { font-family: "Roboto", sans-serif; font-weight: 300; font-size: 76px; line-height: 1; color: var(--red); }
</style>
</head>
<body>
<main class="tote-front">
  <section class="welcome-stack" aria-label="Welcome in many Asian languages">
    <div class="row">
      <span class="word cantonese red" style="font-size:40px;">歡迎</span>
      <span class="word latin silver" style="font-size:30px;">SELAMAT DATANG</span>
      <span class="word korean white" style="font-size:34px;">환영합니다</span>
    </div>
    <div class="row">
      <span class="word thai white" style="font-size:40px;">ยินดีต้อนรับ</span>
      <span class="word japanese red" style="font-size:44px;">ようこそ</span>
    </div>
    <div class="rule" aria-hidden="true"></div>
    <h1 class="welcome-main">WELCOME</h1>
    <div class="rule" aria-hidden="true"></div>
    <div class="row">
      <span class="word latin red" style="font-size:44px;">CHÀO MỪNG</span>
      <span class="word chinese silver" style="font-size:48px;">欢迎</span>
      <span class="word latin white" style="font-size:34px;">MABUHAY</span>
    </div>
    <div class="row">
      <span class="word latin silver" style="font-size:32px;">ТАВТАЙ МОРИЛНО УУ</span>
      <span class="word arabic red" style="font-size:40px;">أهلا بك</span>
    </div>
    <div class="row">
      <span class="word korean red" style="font-size:30px;">환영</span>
      <span class="word japanese silver" style="font-size:30px;">いらっしゃいませ</span>
      <span class="word chinese white" style="font-size:30px;">欢迎光临</span>
    </div>
  </section>

  <div class="brand">
    <span class="brand-dot" aria-hidden="true"></span>
    <span class="brand-name">Dalton's</span>
  </div>
</main>
</body>
</html>
```